Design einer Preisliste
Zielgruppe
Wir produzieren und verkaufen Suppen Konserven und Konzentrate an Gewerbetreibende + Endabnehmer.
Wir sind im Premium Segment angesiedelt.
Hauptsächlicher Vertrieb erfolgt über den Großhandel
Die Firma ist über 80 Jahre alt
https://www.pralm-eintopf.de/
Aufgabenstellung
Unsere Preisliste soll neu designed werden.
Vorgaben sind:
Hochwertig + Elegant
Eher konservativ gehalten als zu bunt.
Die neuen Preise müssen in die Liste mit eingepflegt werden
Die alte Preisliste und die neuen Preise werden mit beigefügt.

```html
<!DOCTYPE html>
<html lang="de">
<head>
<meta charset="utf-8">
<title>Pralm Großverbraucher Sortimentliste</title>
<link rel="stylesheet" href="https://fonts.googleapis.com/css2?family=Montserrat:wght@300;400;500;600;700&family=Great+Vibes&display=swap">
<style>
:root{
  --bg:#e9eaec;
  --paper:#ffffff;
  --dark:#2f3033;
  --ink:#3a3a3a;
  --muted:#8a8a8a;
  --gold:#b8974f;
  --beige:#f1ece1;
  --red:#d9141b;
  --green:#3fae2a;
  --salmon:#ef8a6d;
}
*{box-sizing:border-box;margin:0;padding:0}
html,body{width:1200px;height:2400px;overflow:hidden}
body{background:var(--bg);font-family:'Montserrat',sans-serif;color:var(--ink);position:relative}
.spread{position:absolute;left:22px;top:350px;width:1156px;display:grid;grid-template-columns:570px 570px;gap:16px}
.page{width:570px;height:840px;background:var(--paper);position:relative;overflow:hidden;box-shadow:0 2px 8px rgba(0,0,0,.12)}

/* cover */
.cover{background:linear-gradient(180deg,#2b2c2f 0%,#34353a 40%,#3a3b3f 100%);color:#fff}
.cover-photo{position:absolute;left:0;top:260px;width:570px;height:580px;
  background:radial-gradient(ellipse at 48% 45%,#e8a35a 0 18%,#c27a36 22%,#1f1f22 38%,#2a2b2f 60%,#3b3c40 100%)}
.cover-brand{position:absolute;top:48px;left:0;width:100%;text-align:center}
.wordmark{font-family:'Montserrat',sans-serif;font-weight:700;letter-spacing:2px}
.cover-brand .wordmark{font-size:40px;color:#fff}
.cover-title{position:absolute;top:148px;width:100%;text-align:center}
.cover-title h1{font-weight:500;font-size:24px;letter-spacing:1px}
.cover-title .sub{display:flex;align-items:center;justify-content:center;gap:10px;font-weight:300;font-size:24px;margin-top:2px}
.cover-title .sub::before,.cover-title .sub::after{content:"";width:50px;height:2px;background:var(--gold)}
.cover-badge{position:absolute;left:385px;top:250px;width:145px;height:145px;border-radius:50%;background:var(--gold);box-shadow:0 0 0 4px rgba(184,151,79,.35)}
.cover-valid{position:absolute;bottom:40px;left:220px;font-size:11px;font-weight:500}

/* inner pages */
.head{position:absolute;top:14px;left:0;right:0;height:20px;display:flex;align-items:center;justify-content:flex-end}
.head .wordmark{color:var(--ink);font-size:12px}
.head .tag{font-size:7px;color:var(--gold);font-weight:600;margin:0 10px 0 8px}
.head .tag span{font-weight:300}
.head .num{background:var(--gold);color:#fff;font-size:10px;width:68px;height:16px;display:flex;align-items:center;justify-content:center;font-weight:500}
.content{position:absolute;top:42px;left:0;right:0}
.sec{margin-top:8px}
.sec-title{display:flex;align-items:center;gap:8px}
.sec-title h2{background:var(--dark);color:#fff;font-size:12px;font-weight:600;padding:5px 18px 5px 40px;min-width:180px}
.sec-title .note{font-size:6px;color:var(--muted)}
.sec-title .pill{color:#fff;font-size:8px;font-weight:600;padding:4px 6px}
.pill.veg{background:var(--green)}
.pill.sea{background:var(--salmon)}
.sec-title .script{font-family:'Great Vibes',cursive;color:var(--gold);font-size:18px}
table.price{width:510px;margin:4px 0 0 40px;border-collapse:collapse;font-size:6px;line-height:1.3}
.price th{font-weight:600;font-size:5.5px;color:var(--ink);padding:2px 2px;border-bottom:1px solid var(--gold);text-align:center;vertical-align:bottom}
.price th:first-child{width:36%}
.price td{padding:3px 2px;text-align:center;vertical-align:middle;color:#555;border-bottom:2px solid #fff}
.price tr:nth-child(even) td{background:var(--beige)}
.price td:first-child{text-align:left;padding-left:6px}
.price b{font-weight:600;color:var(--ink);font-size:6.6px}
.price em{font-style:normal;color:var(--gold)}
.price .veg-note{color:var(--green)}
.price small{display:block;font-size:4.8px;color:var(--muted)}
.price .inl{display:inline;font-size:4.8px;color:var(--muted);margin-left:3px}
.redbar{position:absolute;bottom:12px;right:0;background:var(--red);color:#fff;font-size:6px;font-weight:600;padding:5px 14px}
.terms-head{background:var(--gold);color:#fff;text-align:center;font-size:10px;font-weight:600;padding:5px;margin-top:14px}
.terms{font-size:6px;line-height:1.5;color:#555;padding:8px 40px}
.foot{position:absolute;left:0;right:0;bottom:0;height:64px;background:var(--dark);color:#fff;display:flex;align-items:center;padding:0 40px;gap:36px;font-size:7px;line-height:1.4}
.foot b{font-weight:600}
.foot .web{font-weight:600}
.foot .wordmark{margin-left:auto;font-size:16px;color:#fff}
</style>
</head>
<body>
<main class="spread">

  <section class="page cover">
    <div class="cover-photo" role="img" aria-label="Foto: cremige Suppe mit Croûtons und Schnittlauch in schwarzem Gusseisentopf auf dunklem Stein"></div>
    <div class="cover-brand"><span class="wordmark">pralm</span></div>
    <div class="cover-title">
      <h1>GROSSVERBRAUCHER</h1>
      <div class="sub">Sortimentliste</div>
    </div>
    <div class="cover-badge" role="img" aria-label="Goldene Plakette mit Schriftzug: für die gehobene Gastronomie"></div>
    <p class="cover-valid">Preise gültig ab 2022 | 01</p>
  </section>

  <section class="page">
    <header class="head"><span class="wordmark">pralm</span><span class="tag">GROSSVERBRAUCHER <span>| Sortimentliste</span></span><span class="num">2 / 4</span></header>
    <div class="content">
      <div class="sec">
        <div class="sec-title"><h2>Konzentrierte Suppen</h2></div>
        <table class="price">
          <tr><th>Artikel-<br>bezeichnung</th><th>pralm-<br>Nr.</th><th>Dosengröße<br>je Artikel</th><th>Inhalt<br>Dose</th><th>Euro<br>Dose</th><th>maximale<br>Ergiebigkeit</th><th>Karton<br>Inhalt</th><th>C+C Einheit<br>EAN 41877-</th><th>Preis €<br>Karton</th></tr>
          <tr><td><b>Hühnersuppe <em>Premium</em></b><small>mit großer Fleischeinlage, Spitzenqualität,<br>stark konzentriert, 1:8 verdünnen</small></td><td>110-1<br>111-1</td><td>1/4 Dose<br>1/1 Dose</td><td>212 ml<br>850 ml</td><td>3,60<br>11,40</td><td>1,50 l<br>6,00 l</td><td>50 × 10 × 5<br>12 × 12 × 1</td><td>00 71102 3<br>00 71118 4</td><td>180,00<br>136,80</td></tr>
          <tr><td><b>Geb. Ochsenschwanz EXTRA</b><small>mit extra viel Fleischeinlage,<br>konzentriert, 1:1 verdünnen</small></td><td>120-1<br>121-1<br>122-1</td><td>1/4 Dose<br>1/1 Dose<br>5/1 Dose</td><td>212 ml<br>850 ml<br>4250 ml</td><td>1,60<br>4,95<br>18,25</td><td>0,45 l<br>1,80 l<br>9,00 l</td><td>50 × 10 × 5<br>12 × 12 × 1<br>2 × 2 × 1</td><td>00 71205 7<br>00 71213 2<br>00 71221 6</td><td>80,00<br>59,40<br>36,50</td></tr>
          <tr><td><b>Ung. Gulaschsuppe GOLD</b><small>mit doppelter Fleischeinlage,<br>konzentriert, 1:1 verdünnen</small></td><td>130-1<br>131-1<br>132-1</td><td>1/4 Dose<br>1/1 Dose<br>5/1 Dose</td><td>212 ml<br>850 ml<br>2650 ml</td><td>1,85<br>6,05<br>16,25</td><td>0,45 l<br>1,80 l<br>5,70 l</td><td>50 × 10 × 5<br>12 × 12 × 1<br>4 × 4 × 1</td><td>00 71304 1<br>00 71312 8<br>00 71320 3</td><td>92,50<br>72,60<br>65,00</td></tr>
          <tr><td><b>Ung. Gulaschsuppe EXTRA</b><small>mit extra viel Fleischeinlage,<br>konzentriert, 1:1 verdünnen</small></td><td>140-1<br>141-1<br>142-1<br>143-1</td><td>1/4 Dose<br>1/1 Dose<br>3/1 Dose<br>5/1 Dose</td><td>212 ml<br>850 ml<br>2650 ml<br>4250 ml</td><td>1,60<br>5,05<br>14,45<br>22,45</td><td>0,45 l<br>1,80 l<br>5,70 l<br>9,00 l</td><td>50 × 10 × 5<br>12 × 12 × 1<br>4 × 4 × 1<br>2 × 2 × 1</td><td>00 71406 5<br>00 71414 0<br>00 71422 5<br>00 71430 9</td><td>80,00<br>60,60<br>57,80<br>44,90</td></tr>
          <tr><td><b>Ung. Gulaschsuppe I</b><small>mit reichlich Fleischeinlage,<br>konzentriert, 1:1 verdünnen</small></td><td>150-1</td><td>5/1 Dose</td><td>4250 ml</td><td>20,75</td><td>9,00 l</td><td>2 × 2 × 1</td><td>00 71507 4</td><td>41,50</td></tr>
          <tr><td><b>Klare Rindfleischsuppe <em>Premium</em></b><small>mit großer Fleischeinlage, Spitzenqualität,<br>stark konzentriert, 1:6 verdünnen</small></td><td>160-1<br>161-1</td><td>1/4 Dose<br>1/1 Dose</td><td>212 ml<br>850 ml</td><td>3,60<br>11,40</td><td>1,50 l<br>6,00 l</td><td>50 × 10 × 5<br>12 × 12 × 1</td><td>00 71603 9<br>00 71611 4</td><td>180,00<br>136,80</td></tr>
        </table>
      </div>
      <div class="sec">
        <div class="sec-title"><h2>Suppenbasis/Fonds</h2></div>
        <table class="price">
          <tr><th>Artikel-<br>bezeichnung</th><th>pralm-<br>Nr.</th><th>Dosengröße<br>je Artikel</th><th>Inhalt<br>Dose</th><th>Euro<br>Dose</th><th>maximale<br>Ergiebigkeit</th><th>Karton<br>Inhalt</th><th>C+C Einheit<br>EAN 41877-</th><th>Preis €<br>Karton</th></tr>
          <tr><td><b>Hühnersuppe 1:10</b><small>ohne Fleisch<br>1/4 Dose = 2 Liter Suppenbasis<br>1/1 Dose = 8 Liter Suppenbasis oder 5 Liter Saucenfond</small></td><td>210-1<br>211-1</td><td>1/4 Dose<br>1/1 Dose</td><td>212 ml<br>850 ml</td><td>2,00<br>7,05</td><td>2,00 l<br>8,00 l</td><td>50 × 10 × 5<br>12 × 12 × 1</td><td>00 72102 1<br>00 72110 6</td><td>100,00<br>84,60</td></tr>
          <tr><td><b>Rindersuppe 1:10</b><small>ohne Fleisch<br>1/4 Dose = 2 Liter Suppenbasis<br>1/1 Dose = 8 Liter Suppenbasis oder 5 Liter Saucenfond</small></td><td>212-1<br>213-1</td><td>1/4 Dose<br>1/1 Dose</td><td>212 ml<br>850 ml</td><td>2,00<br>7,05</td><td>2,00 l<br>8,00 l</td><td>50 × 10 × 5<br>12 × 12 × 1</td><td>00 72128 1<br>00 72136 6</td><td>100,00<br>84,60</td></tr>
          <tr><td><b>Klare Gemüsesuppe 1:10</b><small>rein vegetarisch, diätisch<br>8 Liter Suppenbasis oder 5 Liter Saucenfond</small></td><td>214-1</td><td>1/1 Dose</td><td>850 ml</td><td>7,05</td><td>8,00 l</td><td>12 × 1</td><td>00 72144 2</td><td>84,60</td></tr>
          <tr><td><b>Klare Fischsuppe 1:5</b><small>4 Liter Suppenbasis oder 2 Liter Saucenfond</small></td><td>215-1</td><td>1/1 Dose</td><td>850 ml</td><td>7,05</td><td>5,00 l</td><td>12 × 1</td><td>00 72152 7</td><td>84,60</td></tr>
          <tr><td><b>Wild-Kraft-Fond 1:5</b><small>4 Liter Suppenbasis oder 2 Liter Saucenfond</small></td><td>216-1</td><td>1/1 Dose</td><td>850 ml</td><td>7,05</td><td>5,00 l</td><td>12 × 1</td><td>00 72160 2</td><td>84,60</td></tr>
          <tr><td><b>Kalbs-Kraft-Fond 1:5</b><small>ohne Fleisch<br>4 Liter Suppenbasis oder 2 Liter Saucenfond</small></td><td>217-1</td><td>1/1 Dose</td><td>850 ml</td><td>6,95</td><td>5,00 l</td><td>12 × 1</td><td>00 72178 7</td><td>83,40</td></tr>
          <tr><td><b>Rindfleischsuppe 1:12</b><small>ohne Fett, ohne Fleisch<br>10 Liter Suppenbasis</small></td><td>218-1</td><td>1/1 Dose</td><td>850 ml</td><td>7,05</td><td>10,00 l</td><td>12 × 1</td><td>00 72186 2</td><td>84,60</td></tr>
          <tr><td><b>Hühnersuppe 1:12</b><small>ohne Fett, ohne Fleisch<br>10 Liter Suppenbasis</small></td><td>219-1</td><td>1/1 Dose</td><td>850 ml</td><td>7,05</td><td>10,00 l</td><td>12 × 1</td><td>00 72194 7</td><td>84,60</td></tr>
        </table>
      </div>
      <div class="sec">
        <div class="sec-title"><h2>Tafelfertige Suppen</h2></div>
        <table class="price">
          <tr><th>Artikel-<br>bezeichnung</th><th>pralm-<br>Nr.</th><th>Dosengröße<br>je Artikel</th><th>Inhalt<br>Dose</th><th>Euro<br>Dose</th><th>maximale<br>Ergiebigkeit</th><th>Karton<br>Inhalt</th><th>C+C Einheit<br>EAN 41877-</th><th>Preis €<br>Karton</th></tr>
          <tr><td><b>Klare Oxtail GOLD <em>Premium</em></b><small>eine international geschätzte Vorspeise</small></td><td>310-1<br>311-1</td><td>1/4 Ring-Pull<br>1/1 Dose</td><td>212 ml<br>850 ml</td><td>1,90<br>5,45</td><td>1 Portion<br>4 Portionen</td><td>50 × 10 × 5<br>12 × 12 × 1</td><td>00 73105 8<br>00 73113 3</td><td>95,00<br>65,40</td></tr>
          <tr><td><b>Franz. Zwiebelsuppe <em>Premium</em></b><small>gebunden, aus frischen Zwiebeln, mit franz. Rotwein</small></td><td>312-1<br>313-1</td><td>1/4 Ring-Pull<br>1/1 Dose</td><td>212 ml<br>850 ml</td><td>1,40<br>3,80</td><td>1 Portion<br>4 Portionen</td><td>50 × 10 × 5<br>12 × 12 × 1</td><td>00 73121 8<br>00 73139 3</td><td>70,00<br>45,60</td></tr>
          <tr><td><b>Tomaten-Creme <em>Premium</em></b><small>leuchtend rot, ohne Einlage</small></td><td>314-1<br>315-1</td><td>1/4 Ring-Pull<br>1/1 Dose</td><td>212 ml<br>850 ml</td><td>1,40<br>3,75</td><td>1 Portion<br>4 Portionen</td><td>50 × 10 × 5<br>12 × 12 × 1</td><td>00 73147 8<br>00 73155 3</td><td>70,00<br>45,00</td></tr>
          <tr><td><b>Kessel Gulasch-Suppe</b><small>mit rustikaler Einlage</small></td><td>316-1<br>317-1</td><td>1/4 Ring-Pull<br>1/1 Dose</td><td>212 ml<br>850 ml</td><td>1,40<br>3,80</td><td>1 Portion<br>4 Portionen</td><td>50 × 10 × 5<br>12 × 12 × 1</td><td>00 73163 8<br>00 73171 3</td><td>70,00<br>45,60</td></tr>
        </table>
      </div>
    </div>
    <div class="redbar">Alle unsere Produkte haben eine garantierte Restlaufzeit von 30 Monaten.</div>
  </section>

  <section class="page">
    <header class="head"><span class="wordmark">pralm</span><span class="tag">GROSSVERBRAUCHER <span>| Sortimentliste</span></span><span class="num">3 / 4</span></header>
    <div class="content">
      <div class="sec">
        <div class="sec-title"><h2>Einzelportion Ringpull-Dosen</h2><span class="note">auch in 24/4 Kartons erhältlich</span></div>
        <table class="price">
          <tr><th>Artikel-<br>bezeichnung</th><th>pralm-<br>Nr.</th><th>Dosengröße<br>je Artikel</th><th>Inhalt<br>Dose</th><th>Euro<br>Dose</th><th>Karton<br>Inhalt</th><th>C+C Einheit<br>EAN 41877-</th><th>Preis €<br>Karton</th></tr>
          <tr><td><b>Hühnersuppe Klar <em>Premium</em></b></td><td>401-1</td><td>1/4 Dose</td><td>212 ml</td><td>1,40</td><td>50 × 10 × 5</td><td>00 74018 2</td><td>70,00</td></tr>
          <tr><td><b>Rindsuppe</b><span class="inl">mit Eierstich &amp; Nudeln</span></td><td>402-1</td><td>1/4 Dose</td><td>212 ml</td><td>1,40</td><td>50 × 10 × 5</td><td>00 74026 7</td><td>70,00</td></tr>
          <tr><td><b>Hühnersuppe</b><span class="inl">mit Prinzessnudeln</span></td><td>403-1</td><td>1/4 Dose</td><td>212 ml</td><td>1,40</td><td>50 × 10 × 5</td><td>00 74034 2</td><td>70,00</td></tr>
          <tr><td><b>Hühnersuppe</b><span class="inl">mit Eierstich &amp; Reis</span></td><td>404-1</td><td>1/4 Dose</td><td>212 ml</td><td>1,40</td><td>50 × 10 × 5</td><td>00 74042 7</td><td>70,00</td></tr>
          <tr><td><b>Tomatensuppe</b><span class="inl">mit Fleischklößchen &amp; Reis</span></td><td>405-1</td><td>1/4 Dose</td><td>212 ml</td><td>1,40</td><td>50 × 10 × 5</td><td>00 74050 2</td><td>70,00</td></tr>
          <tr><td><b>Serb. Bohnensuppe <em>Select</em></b><span class="inl">mit Fleischklößchen &amp; Reis</span></td><td>406-1</td><td>1/4 Dose</td><td>212 ml</td><td>1,40</td><td>50 × 10 × 5</td><td>00 74068 7</td><td>70,00</td></tr>
          <tr><td><b>Geb. Ochsenschwanz</b><span class="inl">mit doppelter Einlage</span></td><td>407-1</td><td>1/4 Dose</td><td>212 ml</td><td>1,40</td><td>50 × 10 × 5</td><td>00 74076 2</td><td>70,00</td></tr>
          <tr><td><b>Gulaschsuppe</b><span class="inl">mit doppelter Einlage</span></td><td>408-1</td><td>1/4 Dose</td><td>212 ml</td><td>1,40</td><td>50 × 10 × 5</td><td>00 74084 7</td><td>70,00</td></tr>
          <tr><td><b>Kessel Gulasch-Suppe</b></td><td>409-1</td><td>1/4 Dose</td><td>212 ml</td><td>1,40</td><td>50 × 10 × 5</td><td>00 74092 2</td><td>70,00</td></tr>
          <tr><td><b>Grüne Pfeffersuppe »Tropenpfeffer«</b></td><td>410-1</td><td>1/4 Dose</td><td>212 ml</td><td>1,40</td><td>50 × 10 × 5</td><td>00 74100 4</td><td>70,00</td></tr>
          <tr><td><b>Markklößchensuppe <em>Select</em></b></td><td>411-1</td><td>1/4 Dose</td><td>212 ml</td><td>1,40</td><td>50 × 10 × 5</td><td>00 74118 9</td><td>70,00</td></tr>
          <tr><td><b>Schwäbische Maultaschen-Suppe</b></td><td>412-1</td><td>1/4 Dose</td><td>212 ml</td><td>1,40</td><td>50 × 10 × 5</td><td>00 74126 4</td><td>70,00</td></tr>
          <tr><td><b>Minestrone Rustica</b><span class="inl">deftig rustikal</span></td><td>413-1</td><td>1/4 Dose</td><td>212 ml</td><td>1,50</td><td>50 × 10 × 5</td><td>00 74134 9</td><td>75,00</td></tr>
          <tr><td><b>Feinschmecker Topf Huhn</b></td><td>414-1</td><td>1/4 Dose</td><td>212 ml</td><td>1,50</td><td>50 × 10 × 5</td><td>00 74142 4</td><td>75,00</td></tr>
          <tr><td><b>Feinschmecker Topf Rind <em>Premium</em></b></td><td>415-1</td><td>1/4 Dose</td><td>212 ml</td><td>1,50</td><td>50 × 10 × 5</td><td>00 74150 9</td><td>75,00</td></tr>
          <tr><td><b>Leberknödel-Suppe</b></td><td>416-1</td><td>1/4 Dose</td><td>212 ml</td><td>1,40</td><td>50 × 10 × 5</td><td>00 74168 4</td><td>70,00</td></tr>
          <tr><td><b>Pfifferling-Creme-Suppe <em>Premium</em></b></td><td>417-1</td><td>1/4 Dose</td><td>212 ml</td><td>1,75</td><td>50 × 10 × 5</td><td>00 74176 9</td><td>87,50</td></tr>
        </table>
      </div>
      <div class="sec">
        <div class="sec-title"><h2>Einzelportion Ringpull-Dosen</h2><span class="pill veg">100 % vegetarisch</span></div>
        <table class="price">
          <tr><th>Artikel-<br>bezeichnung</th><th>pralm-<br>Nr.</th><th>Dosengröße<br>je Artikel</th><th>Inhalt<br>Dose</th><th>Euro<br>Dose</th><th>Karton<br>Inhalt</th><th>C+C Einheit<br>EAN 41877-</th><th>Preis €<br>Karton</th></tr>
          <tr><td><b>Broccoli-Creme-Suppe</b></td><td>421-1</td><td>1/4 Dose</td><td>212 ml</td><td>1,40</td><td>50 × 10 × 5</td><td>00 74217 9</td><td>70,00</td></tr>
          <tr><td><b>Möhren-Ingwer-Suppe</b></td><td>422-1</td><td>1/4 Dose</td><td>212 ml</td><td>1,40</td><td>50 × 10 × 5</td><td>00 74225 4</td><td>70,00</td></tr>
          <tr><td><b>Kürbis-Mango-Creme</b></td><td>423-1</td><td>1/4 Dose</td><td>212 ml</td><td>1,40</td><td>50 × 10 × 5</td><td>00 74233 9</td><td>70,00</td></tr>
          <tr><td><b>Fruchtige Tomatensuppe</b></td><td>424-1</td><td>1/4 Dose</td><td>212 ml</td><td>1,40</td><td>50 × 10 × 5</td><td>00 74241 4</td><td>70,00</td></tr>
          <tr><td><b>Klare Zwiebelsuppe</b></td><td>425-1</td><td>1/4 Dose</td><td>212 ml</td><td>1,40</td><td>50 × 10 × 5</td><td>00 74259 9</td><td>70,00</td></tr>
          <tr><td><b>Champignon-Creme-Suppe</b></td><td>426-1</td><td>1/4 Dose</td><td>212 ml</td><td>1,40</td><td>50 × 10 × 5</td><td>00 74267 4</td><td>70,00</td></tr>
          <tr><td><b>Tomaten-Creme <em>Premium</em></b></td><td>427-1</td><td>1/4 Dose</td><td>212 ml</td><td>1,40</td><td>50 × 10 × 5</td><td>00 74275 9</td><td>70,00</td></tr>
          <tr><td><b>Spargel-Creme-Suppe</b></td><td>428-1</td><td>1/4 Dose</td><td>212 ml</td><td>1,50</td><td>50 × 10 × 5</td><td>00 74283 4</td><td>75,00</td></tr>
        </table>
      </div>
      <div class="sec">
        <div class="sec-title"><h2>Einzelportion Ringpull-Dosen</h2><span class="pill sea">Seafood</span></div>
        <table class="price">
          <tr><th>Artikel-<br>bezeichnung</th><th>pralm-<br>Nr.</th><th>Dosengröße<br>je Artikel</th><th>Inhalt<br>Dose</th><th>Euro<br>Dose</th><th>Karton<br>Inhalt</th><th>C+C Einheit<br>EAN 41877-</th><th>Preis €<br>Karton</th></tr>
          <tr><td><b>Feine Lachs-Creme <em>Select</em></b><span class="inl">aus Wildlachs-Filet</span></td><td>431-1</td><td>1/4 Dose</td><td>212 ml</td><td>1,80</td><td>50 × 10 × 5</td><td>00 74316 9</td><td>90,00</td></tr>
          <tr><td><b>Hummersuppe »Nordmeer«</b><span class="inl">mit einer Schere aus Krabbenfleisch</span></td><td>432-1</td><td>1/4 Dose</td><td>212 ml</td><td>1,80</td><td>50 × 10 × 5</td><td>00 74324 4</td><td>90,00</td></tr>
          <tr><td><b>Nordsee-Krabbensuppe</b><span class="inl">mit 25 g Tiefsee-Krabben 1. Wahl</span></td><td>433-1</td><td>1/4 Dose</td><td>212 ml</td><td>1,90</td><td>50 × 10 × 5</td><td>00 74332 9</td><td>95,00</td></tr>
          <tr><td><b>Nordsee-Krabbensuppe</b><span class="inl">mit 25 g Küsten-Krabben 1. Wahl</span></td><td>434-1</td><td>1/4 Dose</td><td>212 ml</td><td>2,05</td><td>50 × 10 × 5</td><td>00 74340 4</td><td>102,50</td></tr>
        </table>
      </div>
    </div>
    <div class="redbar">Alle unsere Produkte haben eine garantierte Restlaufzeit von 30 Monaten.</div>
  </section>

  <section class="page">
    <header class="head"><span class="wordmark">pralm</span><span class="tag">GROSSVERBRAUCHER <span>| Sortimentliste</span></span><span class="num">4 / 4</span></header>
    <div class="content">
      <div class="sec">
        <div class="sec-title"><h2>2-Portionen Suppen</h2></div>
        <table class="price">
          <tr><th>Artikel-<br>bezeichnung</th><th>pralm-<br>Nr.</th><th>Dosengröße<br>je Artikel</th><th>Inhalt<br>Dose</th><th>Euro<br>Dose</th><th>Karton<br>Inhalt</th><th>C+C Einheit<br>EAN 41877-</th><th>Preis €<br>Karton</th></tr>
          <tr><td><b>Kessel-Gulaschsuppe</b><small>mit rustikaler Einlage</small></td><td>501-1</td><td>1/2 Dose</td><td>425 ml</td><td>1,95</td><td>12 × 1</td><td>00 75014 6</td><td>23,40</td></tr>
          <tr><td><b>Klare Zwiebelsuppe »Pariser Art«</b> <span class="veg-note">100 % vegetarisch</span><small>nach französischer Art mit Weißwein</small></td><td>502-1</td><td>1/2 Dose</td><td>425 ml</td><td>1,95</td><td>12 × 1</td><td>00 75022 1</td><td>23,40</td></tr>
          <tr><td><b>Hühnersuppe</b><small>Consommé mit Anmut und Charakter, mit Eierstich &amp; Reis</small></td><td>503-1</td><td>1/2 Dose</td><td>425 ml</td><td>1,95</td><td>12 × 1</td><td>00 75030 6</td><td>23,40</td></tr>
          <tr><td><b>Fruchtige Tomaten-Creme-Suppe</b> <span class="veg-note">100 % vegetarisch</span><small>Provençale mit Tomatenwürfeln</small></td><td>504-1</td><td>1/2 Dose</td><td>425 ml</td><td>1,95</td><td>12 × 1</td><td>00 75048 1</td><td>23,40</td></tr>
        </table>
      </div>
      <div class="sec">
        <div class="sec-title"><h2>Bouillon Ringpull-Dosen</h2></div>
        <table class="price">
          <tr><th>Artikel-<br>bezeichnung</th><th>pralm-<br>Nr.</th><th>Dosengröße<br>je Artikel</th><th>Inhalt<br>Dose</th><th>Euro<br>Dose</th><th>Karton<br>Inhalt</th><th>C+C Einheit<br>EAN 41877-</th><th>Preis €<br>Karton</th></tr>
          <tr><td><b>Rindbouillon</b><small>kräftig, nach Küchenmeister Art, zum Kochen &amp; Würzen, 20 g/Liter</small></td><td>511-1</td><td>1 kg</td><td>für 50 l</td><td>10,95</td><td>6 × 1</td><td>00 75113 6</td><td>65,70</td></tr>
          <tr><td><b>Hühnerbouillon doppelt</b><small>aus besten Zutaten, 40 g/Liter</small></td><td>512-1</td><td>1 kg</td><td>für 25 l</td><td>12,35</td><td>6 × 1</td><td>00 75121 1</td><td>74,10</td></tr>
        </table>
      </div>
      <div class="sec">
        <div class="sec-title"><h2>Suppeneinlagen</h2></div>
        <table class="price">
          <tr><th>Artikel-<br>bezeichnung</th><th>pralm-<br>Nr.</th><th>Dosengröße<br>je Artikel</th><th>Inhalt<br>Dose</th><th>Euro<br>Dose</th><th>Karton<br>Inhalt</th><th>C+C Einheit<br>EAN 41877-</th><th>Preis €<br>Karton</th></tr>
          <tr><td><b>Eierstich <em>Premium</em></b><small>gewürfelt, nach Küchenmeister Art</small></td><td>521-1</td><td>1/1 Dose</td><td>500 g</td><td>6,45</td><td>12 × 1</td><td>00 75212 6</td><td>77,40</td></tr>
          <tr><td><b>Markklößchen <em>Premium</em></b><small>bestechend im Aussehen - delikat im Geschmack</small></td><td>522-1</td><td>1/1 Dose</td><td>100 Klößchen</td><td>7,50</td><td>12 × 1</td><td>00 75220 1</td><td>90,00</td></tr>
        </table>
      </div>
      <div class="sec">
        <div class="sec-title"><h2>Eintöpfe</h2><span class="script">Spezialitäten aus dem Gemüsegarten</span></div>
        <table class="price">
          <tr><th>Artikel-<br>bezeichnung</th><th>pralm-<br>Nr.</th><th>Dosengröße<br>je Artikel</th><th>Inhalt<br>Dose</th><th>Euro<br>Dose</th><th>Karton<br>Inhalt</th><th>C+C Einheit<br>EAN 41877-</th><th>Preis €<br>Karton</th></tr>
          <tr><td><b>Erbsensuppe - deftig</b></td><td>531-1</td><td>1/1 Dose</td><td>850 ml</td><td>2,65</td><td>12 × 1</td><td>00 75311 6</td><td>31,80</td></tr>
          <tr><td><b>Kartoffelsuppe - rustikal</b></td><td>532-1</td><td>1/1 Dose</td><td>850 ml</td><td>2,65</td><td>12 × 1</td><td>00 75329 1</td><td>31,80</td></tr>
          <tr><td><b>Linsen-Suppe - Terrine</b></td><td>533-1</td><td>1/1 Dose</td><td>850 ml</td><td>2,65</td><td>12 × 1</td><td>00 75337 6</td><td>31,80</td></tr>
        </table>
      </div>
      <div class="sec">
        <div class="sec-title"><h2>Fleischkonserven</h2><span class="script">in hervorragender Qualität</span></div>
        <table class="price">
          <tr><th>Artikel-<br>bezeichnung</th><th>pralm-<br>Nr.</th><th>Dosengröße<br>je Artikel</th><th>Inhalt<br>Dose</th><th>Euro<br>Dose</th><th>Karton<br>Inhalt</th><th>C+C Einheit<br>EAN 41877-</th><th>Preis €<br>Karton</th></tr>
          <tr><td><b>Labskaus nach Seemannsart</b><small>nach Kapitänsart</small></td><td>541-1</td><td>1/1 Dose</td><td>850 ml</td><td>4,45</td><td>12 × 1</td><td>00 75410 6</td><td>53,40</td></tr>
          <tr><td><b>Ragoût fin »Feine Art« <em>Select</em></b><small>aus Kalb &amp; Geflügel, ohne Brät und ohne Farce</small></td><td>542-1<br>543-1</td><td>1/4 Ring-Pull<br>1/1 Dose</td><td>1 große Port.<br>4 große Port.</td><td>3,25<br>10,00</td><td>50 × 10 × 5<br>24 × 1/4<br>12 × 1</td><td>00 75428 1<br>00 75436 6<br>00 75444 1</td><td>162,50<br>78,00<br>120,00</td></tr>
        </table>
      </div>
      <div class="terms-head">Lieferungs- &amp; Zahlungsbedingungen</div>
      <p class="terms">Die Preise verstehen sich frei Haus und ohne MwSt.. Die Ware bleibt bis zur vollständigen Bezahlung unser Eigentum. Sie kann nur im ordnungsgemäßen Geschäftsverkehr weiterveräußert werden. Der Käufer tritt jedoch die Forderung, die sich aus der Weiterveräußerung der Vorbehaltsware ergibt, in jedem Falle an uns ab. Eine Sicherungsübereignung der Vorbehaltsware ist ausgeschlossen. Zahlung 30 Tage nach Rechnungsdatum netto Kasse. Erfüllungsort und Gerichtsstand der Lieferung und Zahlung ist der Sitz der Firma: Pralmer &amp; Co. GmbH &amp; Co. KG, D-40599 Kerndorf.</p>
    </div>
    <footer class="foot">
      <div><b>Pralmer &amp; Co. GmbH &amp; Co. KG</b><br>Lindenauer Straße 12<br>D-40599 Kerndorf</div>
      <div>Telefon : +49-(0)-2100-48230<br>Telefax : +49-(0)-2100-48239<br>E-Mail : info@pralm-eintopf.de</div>
      <div class="web">www.pralm-eintopf.de</div>
      <span class="wordmark">pralm</span>
    </footer>
  </section>

</main>
</body>
</html>
```